Business card design for a dynamic IT consulting company

We need a business card design for a young firm, specialized in the Telecommunications/Consulting industry. The name of the company is Quindor and Partners Business Consulting Ltd. (Short name: Quindor and Partnes)
Quindor = solve read reverse, so we aim to be uncomplicated and solution-oriented. The small pipe in our logo is also related to the word solve. So we need a new business card design, which is simple, eye catching and something non traditional (I would probably prefer a square shaped design rather than a rectangle, but open for suggestions). Attached our logo.

Target Market(s)

Usually our customers are Tier1 Telecoms providers (Q-Netra, Palorix, etc) and their executives.

Industry/Entity Type

Business

Contact Information for Business Card

Name: Bence Tolnavari
Email: b.tolnavari@quindor.hu
Web: www.quindor.hu
Mobile: +36 30 518 2769
Title: Managing Director

Optional:
Company name: Quindor and Partners Ltd.
Address: 1087 Budapest, Tolvenka str. 28/C, Hungary

Font styles to use
Other font styles liked:
• helveticaneue_medium, Prime Regular are used now.

Colors

Designer to choose colors to be used in the design.

Requirements
Must have
• I would like to have a 2 sided design.
Nice to have
• I thought if we make the logo a bit bigger (without the company name), that could go to the back with the company name below. I though, if the pipe in the logo is somehow touchable on the business card, would be nice and unique.

```html
<!DOCTYPE html>
<html lang="en">
<head>
<meta charset="utf-8">
<title>Quindor and Partners – Business Card</title>
<link rel="stylesheet" href="https://fonts.googleapis.com/css2?family=Work+Sans:wght@400;600&display=swap">
<style>
  :root {
    --page-bg: #1c1c1d;
    --card-white: #ffffff;
    --card-grey: #5e5f61;
    --brand-blue: #1a9ad6;
    --brand-magenta: #a8288f;
    --ink-grey: #6b6b6e;
    --rule-grey: #8a8a8c;
    --back-text: #eeeeee;
  }
  * { box-sizing: border-box; margin: 0; padding: 0; }
  html, body {
    width: 1200px; height: 963px; overflow: hidden;
    background: var(--page-bg);
    font-family: "Work Sans", Arial, sans-serif;
  }
  .sheet {
    width: 1200px; height: 963px;
    display: flex; flex-direction: column;
    align-items: center; justify-content: center; gap: 40px;
  }
  .card {
    position: relative;
    width: 700px; height: 424px;
    border-radius: 18px;
    overflow: hidden;
  }
  .card--front { background: var(--card-white); }
  .card--back {
    background: var(--card-grey);
    display: flex; align-items: center; justify-content: center;
  }
  .wave { position: absolute; inset: 0; }
  .front-brand {
    position: absolute; left: 60px; top: 70px;
    display: flex; align-items: center; gap: 14px;
    color: var(--brand-magenta);
    font-weight: 600; font-size: 46px; letter-spacing: 0.5px;
  }
  .brand-square {
    width: 26px; height: 26px; background: var(--brand-blue);
  }
  .divider {
    position: absolute; left: 352px; top: 70px;
    width: 2px; height: 150px; background: var(--rule-grey);
  }
  .contact {
    position: absolute; left: 378px; top: 74px;
    color: var(--ink-grey);
    font-size: 15px; line-height: 1.45;
  }
  .contact__name {
    color: var(--brand-blue);
    font-weight: 600; font-size: 24px; line-height: 1.2;
  }
  .contact__title { margin-bottom: 6px; }
  .contact__address { margin-bottom: 6px; }
  .contact__line { display: flex; align-items: center; gap: 8px; }
  .contact__line svg { width: 13px; height: 13px; flex: none; }
  .back-brand {
    display: flex; align-items: center; gap: 18px;
    color: var(--back-text);
    font-weight: 400; font-size: 50px; letter-spacing: 0.5px;
  }
  .back-square { width: 30px; height: 30px; background: var(--back-text); }
</style>
</head>
<body>
<main class="sheet">
  <section class="card card--front" aria-label="Card front">
    <svg class="wave" viewBox="0 0 700 424" aria-hidden="true">
      <path d="M0 250 C130 305 270 335 390 360 C465 377 505 398 522 424 L0 424 Z" fill="var(--brand-blue)"/>
      <path d="M0 232 C130 292 275 324 398 350 C475 367 515 392 536 424" fill="none" stroke="var(--brand-magenta)" stroke-width="5"/>
    </svg>
    <div class="front-brand"><span class="brand-square"></span>Quindor</div>
    <div class="divider"></div>
    <div class="contact">
      <p class="contact__name">Bence Tolnavari</p>
      <p class="contact__title">Managing Director</p>
      <p class="contact__address">1087 Budapest,<br>Tolvenka str. 28/C, Hungary</p>
      <p class="contact__line">
        <svg viewBox="0 0 16 16"><path d="M4 1 L7 4 L5 6 C6 8.5 7.5 10 10 11 L12 9 L15 12 L13 15 C7 14 2 9 1 3 Z" fill="var(--brand-blue)"/></svg>
        +36 30 518 2769
      </p>
      <p class="contact__line">
        <svg viewBox="0 0 16 16"><rect x="1.5" y="3.5" width="13" height="9" fill="none" stroke="var(--brand-blue)" stroke-width="1.5"/><path d="M1.5 3.5 L8 9 L14.5 3.5" fill="none" stroke="var(--brand-blue)" stroke-width="1.5"/></svg>
        b.tolnavari@quindor.hu
      </p>
      <p class="contact__line">
        <svg viewBox="0 0 16 16"><circle cx="8" cy="8" r="6.5" fill="none" stroke="var(--brand-blue)" stroke-width="1.5"/><path d="M1.5 8 H14.5 M8 1.5 C5 5 5 11 8 14.5 M8 1.5 C11 5 11 11 8 14.5" fill="none" stroke="var(--brand-blue)" stroke-width="1.2"/></svg>
        www.quindor.hu
      </p>
    </div>
  </section>

  <section class="card card--back" aria-label="Card back">
    <div class="back-brand"><span class="back-square"></span>Quindor &amp; Partners</div>
  </section>
</main>
</body>
</html>
```